a customWebsite for our live Escape room with landing page and then links to the multiple locations

We are looking for a new main landing page that then goes to the location site So puzzlevaultery.com (main landing page)
The site needs to have main company info locations to choose a countdown clock and book now option news articles and video, a link to social media.
a link to the locations
the locations page will go to puzzlevaulterydm.com or puzzlevaulterymke.com for the des moines location and the milwaukee location with more locations opening soon. The location pages need to have a one page theme with book now options and social media links. We are a escape room company please visit puzzlevaulterydm.com to get a idea of what we are looking for. We want to work with someone that can also do updates as we add new rooms etc.. Also must be able to design and upload the site to godaddy for us. We would like the countdown timer to display a message at the end (promo code etc) All pages need to link back to the main page and the Des moines Location needs to link to qrtdesmoines.com. We are looking for a interactive responsive site that shows what we are. The room bios for the MKE location will be upfoaded soon the rooms for des moines are on puzzlevaulterydm.com. please google escape rooms and visit competitor sites to help get more ideas we are open to color changes or logo changes we just shared a video and article on facebook to help http://www.prairiegazette-news.com/story/entertainment/2015/02/19/puzzle-vaultery-des-moines/58214706/

Reason: Not one design has had a landing page with the links to the locations etc....

Reason: Still looking for a main page for puzzle vaultery on the main landing page stuff about escape games news stories who should try also a video feed and countdown timmer then a link to des moines and Milwaukee location on the milwaukee page info on the location and the rooms with a book now option. on the des moines location info on the location and rooms with a book now location pages should have links to facebook twitter for that location

Target Market(s)

Customers looking for information about our escape rooms

Industry/Entity Type

It Company

Number of Pages Required

4 page

Requirements
Must have
• main landing page, Des Moines Location Page, Milwaukee Location Page
• booking page
Nice to have
• Be creative look at our page and other pages related to escape rooms to get ideas

```html
<!DOCTYPE html>
<html lang="en">
<head>
<meta charset="utf-8">
<title>Rooms – Puzzle Vaultery Des Moines</title>
<link href="https://fonts.googleapis.com/css2?family=Cantarell:wght@400;700&display=swap" rel="stylesheet">
<style>
  :root {
    --page-bg: #ffffff;
    --heading-red: #c8202a;
    --button-yellow: #ffd925;
    --button-text: #6e5a00;
    --poster-black: #000000;
    --poster-white: #ece8e2;
    --rating-yellow: #f5d21c;
  }
  * { box-sizing: border-box; margin: 0; padding: 0; }
  html, body {
    width: 1200px;
    height: 900px;
    overflow: hidden;
    background: var(--page-bg);
    font-family: "Cantarell", sans-serif;
  }
  .rooms-page { position: relative; width: 1200px; height: 900px; overflow: hidden; }
  .page-title {
    position: absolute; top: 27px; left: 0; width: 100%;
    text-align: center; font-size: 27px; font-weight: 400; line-height: 34px;
    color: var(--heading-red);
  }
  .room-card { position: absolute; width: 238px; }
  .room-name {
    position: absolute; top: 0; left: -60px; width: 358px;
    text-align: center; font-size: 19.5px; font-weight: 400; line-height: 28px;
    color: var(--heading-red);
  }
  .room-capacity {
    position: absolute; top: 42px; left: -60px; width: 358px;
    text-align: center; font-size: 12.5px; line-height: 18px;
    color: var(--heading-red);
  }
  .room-poster {
    position: absolute; top: 62px; left: 0;
    width: 238px; height: 376px;
    background: var(--poster-black);
    overflow: hidden;
    color: var(--poster-white);
  }
  .poster-photo { position: absolute; left: 0; width: 238px; }
  .poster-title {
    position: absolute; left: 0; width: 238px; text-align: center;
    font-weight: 700; color: var(--poster-white); line-height: 1;
  }
  .poster-tagline {
    position: absolute; font-size: 8px; font-style: italic; line-height: 10px;
    color: var(--poster-white);
  }
  .poster-brand {
    position: absolute; left: 0; width: 238px; text-align: center;
    font-size: 11px; font-weight: 700; letter-spacing: 1px; line-height: 13px;
    color: var(--rating-yellow);
  }
  .poster-brand::before {
    content: ""; display: inline-block; width: 9px; height: 9px;
    background: var(--rating-yellow); margin-right: 6px; vertical-align: -1px;
  }
  .poster-ratings { position: absolute; top: 315px; left: 41px; width: 190px; }
  .rating-row { display: flex; align-items: center; height: 12px; }
  .rating-label {
    width: 60px; font-size: 7.5px; font-weight: 700; font-family: Georgia, serif;
    color: #ffffff;
  }
  .rating-bar { height: 1.5px; background: var(--rating-yellow); }
  .room-actions {
    position: absolute; top: 447px; left: 0; width: 238px;
    display: flex; justify-content: space-between;
  }
  .room-button {
    display: block; width: 106px; height: 55px; line-height: 55px;
    text-align: center; background: var(--button-yellow);
    color: var(--button-text); font-size: 14.5px; text-decoration: none;
    border-radius: 2px; white-space: nowrap;
  }
</style>
</head>
<body>
<main class="rooms-page">
  <h1 class="page-title">Rooms</h1>

  <!-- Party Room -->
  <article class="room-card" style="left:117px; top:128px;">
    <h2 class="room-name">Party Room</h2>
    <p class="room-capacity">Min Players 1 – Max Players 12</p>
    <div class="room-poster">
      <p class="poster-title" style="top:14px; font-size:25px;">The Party Room</p>
      <p class="poster-tagline" style="top:45px; right:16px;">Can you make it out in 60 min?</p>
      <div class="poster-photo" style="top:85px; height:145px; background:radial-gradient(ellipse at 12% 15%, #c9ccd8 0%, #4b4d5a 18%, #1d1d22 50%, #050505 100%);" role="img" aria-label="Crowd in a dark club under a stage light"></div>
      <p class="poster-brand" style="top:270px;">PUZZLE VAULTERY DES MOINES</p>
      <div class="poster-ratings">
        <div class="rating-row"><span class="rating-label">Physical</span><span class="rating-bar" style="width:12px"></span></div>
        <div class="rating-row"><span class="rating-label">Team Work</span><span class="rating-bar" style="width:72px"></span></div>
        <div class="rating-row"><span class="rating-label">Fear Factor</span><span class="rating-bar" style="width:3px"></span></div>
        <div class="rating-row"><span class="rating-label">Brain Power</span><span class="rating-bar" style="width:70px"></span></div>
        <div class="rating-row"><span class="rating-label">Fun</span><span class="rating-bar" style="width:96px"></span></div>
      </div>
    </div>
    <div class="room-actions">
      <a class="room-button" href="#">Read scenario</a>
      <a class="room-button" href="#">Book now</a>
    </div>
  </article>

  <!-- The Recruit -->
  <article class="room-card" style="left:473px; top:128px;">
    <h2 class="room-name">The Recruit</h2>
    <p class="room-capacity">Min Players 1 – Max Players 8</p>
    <div class="room-poster">
      <p class="poster-brand" style="top:18px;">PUZZLE VAULTERY DES MOINES</p>
      <div class="poster-photo" style="top:50px; height:170px; background:radial-gradient(ellipse at 50% 45%, #5a534c 0%, #25211d 45%, #000 78%);" role="img" aria-label="Dark dramatic portrait scene"></div>
      <p class="poster-title" style="top:236px; font-size:34px;">The Recruit</p>
      <p class="poster-tagline" style="top:272px; right:20px;">final selection stages for a "Blacklist" division</p>
      <div class="poster-ratings">
        <div class="rating-row"><span class="rating-label">Physical</span><span class="rating-bar" style="width:42px"></span></div>
        <div class="rating-row"><span class="rating-label">Team Work</span><span class="rating-bar" style="width:50px"></span></div>
        <div class="rating-row"><span class="rating-label">Fear Factor</span><span class="rating-bar" style="width:5px"></span></div>
        <div class="rating-row"><span class="rating-label">Brain Power</span><span class="rating-bar" style="width:40px"></span></div>
        <div class="rating-row"><span class="rating-label">Fun</span><span class="rating-bar" style="width:96px"></span></div>
      </div>
    </div>
    <div class="room-actions">
      <a class="room-button" href="#">Read scenario</a>
      <a class="room-button" href="#">Book now</a>
    </div>
  </article>

  <!-- The Collector -->
  <article class="room-card" style="left:846px; top:128px;">
    <h2 class="room-name">The Collector</h2>
    <p class="room-capacity">Min Players 1 – Max Players 12</p>
    <div class="room-poster">
      <div class="poster-photo" style="top:0; height:175px; background:radial-gradient(ellipse at 72% 20%, #b8b4a8 0%, #55514a 22%, #1c1a17 55%, #000 100%);" role="img" aria-label="Silhouettes in a dim hallway near a window"></div>
      <p class="poster-brand" style="top:240px;">PUZZLE VAULTERY DES MOINES</p>
      <p class="poster-title" style="top:268px; font-size:22px; letter-spacing:0.5px;">THE COLLECTOR</p>
      <p class="poster-tagline" style="top:292px; right:20px; font-style:normal; font-weight:700;">CAN YOU ESCAPE?</p>
      <div class="poster-ratings">
        <div class="rating-row"><span class="rating-label">Physical</span><span class="rating-bar" style="width:65px"></span></div>
        <div class="rating-row"><span class="rating-label">Team Work</span><span class="rating-bar" style="width:78px"></span></div>
        <div class="rating-row"><span class="rating-label">Fear Factor</span><span class="rating-bar" style="width:45px"></span></div>
        <div class="rating-row"><span class="rating-label">Brain Power</span><span class="rating-bar" style="width:46px"></span></div>
        <div class="rating-row"><span class="rating-label">Fun</span><span class="rating-bar" style="width:96px"></span></div>
      </div>
    </div>
    <div class="room-actions">
      <a class="room-button" href="#">Read scenario</a>
      <a class="room-button" href="#">Book now</a>
    </div>
  </article>

  <!-- The Cellar -->
  <article class="room-card" style="left:117px; top:676px;">
    <h2 class="room-name">The Cellar</h2>
    <p class="room-capacity">Min Players 1 – Max Players 10</p>
    <div class="room-poster">
      <p class="poster-brand" style="top:12px;">PUZZLE VAULTERY DES MOINES</p>
      <div class="poster-photo" style="top:38px; height:338px; background:linear-gradient(150deg, #000 0%, #1e2528 40%, #3a4245 55%, #0a0a0a 100%);" role="img" aria-label="Shadowy figure on dark cellar stairs"></div>
    </div>
  </article>

  <!-- White Collar -->
  <article class="room-card" style="left:474px; top:676px;">
    <h2 class="room-name">White Collar</h2>
    <p class="room-capacity">Min Players 1 – Max Players 10</p>
    <div class="room-poster">
      <div class="poster-photo" style="top:0; height:376px; background:linear-gradient(180deg, #0a0a0a 0%, #262626 45%, #111 80%, #000 100%);" role="img" aria-label="Noir figure in a hat"></div>
      <p class="poster-title" style="top:12px; font-size:31px;">White Collar</p>
      <p class="poster-tagline" style="top:45px; left:0; width:238px; text-align:center; font-style:normal; font-size:10px; letter-spacing:0.5px;">GOOD LUCK AND GODSPEED.</p>
    </div>
  </article>

  <!-- The Job -->
  <article class="room-card" style="left:846px; top:676px;">
    <h2 class="room-name">The Job</h2>
    <p class="room-capacity">Min Players 1 – Max Players 10</p>
    <div class="room-poster">
      <p class="poster-brand" style="top:12px;">PUZZLE VAULTERY DES MOINES</p>
      <div class="poster-photo" style="top:38px; height:338px; background:radial-gradient(ellipse at 50% 55%, #4d6878 0%, #1a2a35 40%, #000 78%);" role="img" aria-label="Cold blue vault mechanism artwork"></div>
    </div>
  </article>
</main>
</body>
</html>
```